Kelo Wave Mint Business cards

Logo, tag line and photo on card
Agent Name
Title
Address
Phone number
Email
Website
Make logo on one side large by rotating  to portrait format.  Keep the background of the logo white.

Contact Information for Business Card
Slogan; Making Every Wave Count

```html
<!DOCTYPE html>
<html lang="en">
<head>
<meta charset="utf-8">
<title>Kelo Wave Mint – Business Cards</title>
<link rel="stylesheet" href="https://fonts.googleapis.com/css2?family=Montserrat:wght@600;800&family=Open+Sans:wght@400;600&display=swap">
<style>
  :root {
    --stage: #232323;
    --card: #ffffff;
    --navy: #1f2f66;
    --red: #c8232a;
    --ink: #1a1a1a;
    --photo-dark: #141414;
    --photo-mid: #4a3f3a;
  }
  * { box-sizing: border-box; margin: 0; padding: 0; }
  html, body { width: 1200px; height: 711px; overflow: hidden; background: var(--stage); }
  .stage {
    width: 1200px; height: 711px;
    display: flex; justify-content: center; align-items: center; gap: 40px;
  }
  .card {
    width: 290px; height: 507px;
    background: var(--card);
    border-radius: 20px;
    box-shadow: 0 14px 30px rgba(0,0,0,.55);
    position: relative;
    overflow: hidden;
  }
  /* front */
  .card--front { display: flex; align-items: center; justify-content: center; }
  .brand-name {
    font-family: "Montserrat", sans-serif;
    font-weight: 800;
    color: var(--navy);
    line-height: .95;
    text-align: center;
  }
  .brand-name--large { font-size: 58px; letter-spacing: -1px; }
  .brand-name--small { font-size: 19px; letter-spacing: -.3px; }

  /* back */
  .card--back {
    display: flex; flex-direction: column; align-items: center;
    padding-top: 28px;
  }
  .portrait {
    margin-top: 18px;
    width: 136px; height: 136px;
    border-radius: 50%;
    border: 3px solid var(--red);
    background: radial-gradient(circle at 50% 45%, var(--photo-mid) 0%, var(--photo-dark) 62%);
  }
  .agent-name {
    margin-top: 16px;
    font-family: "Montserrat", sans-serif;
    font-weight: 800;
    font-size: 25px;
    letter-spacing: -.3px;
  }
  .agent-name__first { color: var(--red); }
  .agent-name__last { color: var(--navy); }
  .agent-title {
    font-family: "Montserrat", sans-serif;
    font-weight: 600;
    font-size: 13px;
    color: var(--ink);
    margin-top: 2px;
  }
  .dot-row { display: block; margin-top: 10px; }
  .contact-lines {
    font-family: "Open Sans", sans-serif;
    font-size: 12.5px;
    color: var(--ink);
    text-align: center;
    line-height: 1.45;
    margin-top: 6px;
  }
  .slogan {
    margin-top: 12px;
    font-family: "Open Sans", sans-serif;
    font-weight: 600;
    font-size: 13px;
    color: var(--red);
    border: 2px solid var(--red);
    border-radius: 9px;
    padding: 3px 12px;
  }
</style>
</head>
<body>
<main class="stage">

  <section class="card card--front" aria-label="Business card front">
    <h1 class="brand-name brand-name--large">Kelo<br>Wave<br>Mint</h1>
  </section>

  <section class="card card--back" aria-label="Business card back">
    <div class="brand-name brand-name--small">Kelo<br>Wave<br>Mint</div>

    <div class="portrait" role="img" aria-label="Portrait photo of the managing director"></div>

    <h2 class="agent-name"><span class="agent-name__first">Daren</span> <span class="agent-name__last">Holvik</span></h2>
    <p class="agent-title">Managing Director</p>

    <svg class="dot-row" width="260" height="30" viewBox="0 0 260 30" aria-hidden="true">
      <g fill="var(--red)">
        <circle cx="6" cy="15" r="2"/><circle cx="17" cy="15" r="2.6"/><circle cx="29" cy="15" r="3.2"/>
        <circle cx="42" cy="15" r="3.8"/><circle cx="56" cy="15" r="4.4"/><circle cx="71" cy="15" r="5"/>
        <circle cx="189" cy="15" r="5"/><circle cx="204" cy="15" r="4.4"/><circle cx="218" cy="15" r="3.8"/>
        <circle cx="231" cy="15" r="3.2"/><circle cx="243" cy="15" r="2.6"/><circle cx="254" cy="15" r="2"/>
        <circle cx="104" cy="15" r="12"/><circle cx="130" cy="15" r="12"/><circle cx="156" cy="15" r="12"/>
      </g>
      <!-- phone -->
      <path d="M99 9 q-2 1 -1 4 q2 5 7 8 q3 1 4 -1 l-2 -2 q-1 -1 -2 0 q-3 -2 -4 -5 q1 -1 0 -2 z" fill="#fff"/>
      <!-- envelope -->
      <rect x="123" y="10" width="14" height="10" rx="1" fill="none" stroke="#fff" stroke-width="1.6"/>
      <path d="M123 11 l7 5 l7 -5" fill="none" stroke="#fff" stroke-width="1.6"/>
      <!-- globe -->
      <circle cx="156" cy="15" r="7" fill="none" stroke="#fff" stroke-width="1.6"/>
      <ellipse cx="156" cy="15" rx="3" ry="7" fill="none" stroke="#fff" stroke-width="1.3"/>
      <line x1="149" y1="15" x2="163" y2="15" stroke="#fff" stroke-width="1.3"/>
    </svg>

    <p class="contact-lines">(555) 214-0368<br>info@kelowave.com<br>www.kelowave.com</p>

    <svg class="dot-row" width="260" height="30" viewBox="0 0 260 30" aria-hidden="true">
      <g fill="var(--red)">
        <circle cx="8" cy="15" r="2"/><circle cx="20" cy="15" r="2.6"/><circle cx="33" cy="15" r="3.2"/>
        <circle cx="47" cy="15" r="3.8"/><circle cx="62" cy="15" r="4.4"/><circle cx="78" cy="15" r="5"/><circle cx="95" cy="15" r="5.6"/>
        <circle cx="165" cy="15" r="5.6"/><circle cx="182" cy="15" r="5"/><circle cx="198" cy="15" r="4.4"/>
        <circle cx="213" cy="15" r="3.8"/><circle cx="227" cy="15" r="3.2"/><circle cx="240" cy="15" r="2.6"/><circle cx="252" cy="15" r="2"/>
        <circle cx="130" cy="15" r="12"/>
      </g>
      <path d="M130 23 q-6 -6 -6 -10 a6 6 0 0 1 12 0 q0 4 -6 10 z" fill="none" stroke="#fff" stroke-width="1.6"/>
      <circle cx="130" cy="13" r="2" fill="#fff"/>
    </svg>

    <p class="contact-lines">418 Linden Row, Suite 120<br>Millbrook, TX 75930</p>

    <p class="slogan">Making Every Wave Count</p>
  </section>

</main>
</body>
</html>
```